Website Design for a Chemical Sales Company

We are working with a Chemical Sales Company in California. They sell various chemicals throughout the US.
Types of products they sell: https://www.wardenvale.example/us/products/all
https://www.molvista.example/products/kerrin/glacyn-glycol-thermal-fluids/glacyn-propylene-glycol-thermal-fluids
Some sites to use for inspiration:
https://www.molvista.example
https://www.kerrin.example/en-us
Thank you for taking the time to consider designing a website for us. We are web developers based in Stockton, CA, USA. Most of our projects go through the same process. Understanding this process may help you win a project with us. We custom-code all of our websites in-house. We don’t have any requirements as to what tools you use for your design, but we ask that you follow these guidelines.
IMAGES:
If you use any images or icons in the design, we ask that you have a link to the asset so we can purchase the image/icon. Most of the designs we submit do not have the customer’s images on them unless they have some great images. Be creative; show us the feeling you are trying to portray with your image choices. Use any royalty-free site you choose. We subscribe to Pelmora and mainly use their images, but we can purchase images outside of Pelmora. PLEASE NOTE: we will not submit designs to clients with watermarks on the images.
FONTS:
We ask that you identify the fonts you’re using in the design. This can be done in a message if you want. We typically use Google Fonts and Pelmora Fonts.
CONTENT:
We're always open to different content and ideas. We often submit designs with stock images so the client can see our vision. We typically take pictures after the website launch to use their images with our vision. Lorem Ipsum is fine for paragraphs, but we ask that you make the Headers with correct English. We want to be able to show the vision and identify the sections of the website.
INSPIRATION:
We typically add a couple of links in the brief of websites we like to help you get started in your design.
REVISIONS:
We do not often ask for revisions of the designs unless we see something in the design that may not appeal to the client. If there are slight changes that we want to make, we do that in the development process.
FEEDBACK:
We rarely give feedback on designs during the design process. We are working on many website projects and do not have the time to provide feedback. We usually respond if your request is well thought out and asks specific questions, but a note asking “feedback, please” usually goes unanswered.

```html
<!DOCTYPE html>
<html lang="en">
<head>
<meta charset="utf-8">
<title>Nuvexa Link — Chemical Sales</title>
<link rel="stylesheet" href="https://fonts.googleapis.com/css2?family=Poppins:wght@300;400;500;600;700;800&display=swap">
<style>
:root{
  --blue:#0f9ad8;
  --blue-dark:#0b7fc0;
  --ink:#1d1d1f;
  --text:#3a3a3a;
  --grey-bg:#f2f2f2;
  --white:#ffffff;
  --footer:#0b0c0e;
  --line:#7a7a7a;
}
*{margin:0;padding:0;box-sizing:border-box}
html,body{width:1200px;height:4552px;overflow:hidden}
body{font-family:"Poppins",sans-serif;color:var(--text);background:var(--white);position:relative}
.section{position:absolute;left:0;width:1200px}
.abs{position:absolute}
.rule{position:absolute;width:96px;height:3px;background:var(--blue)}
.heading{position:absolute;font-family:"Poppins",sans-serif;font-weight:700;color:var(--blue);letter-spacing:-.5px;line-height:1.1}
.para{position:absolute;font-size:16.5px;line-height:30px;color:var(--text);text-align:justify}
.btn{position:absolute;height:54px;border-radius:27px;background:var(--blue);color:var(--white);font-weight:700;font-size:15px;display:flex;align-items:center;padding-left:30px;letter-spacing:-.2px;text-transform:uppercase}
.btn .circle{position:absolute;right:4px;top:4px;width:46px;height:46px;border-radius:50%;background:var(--white);display:flex;align-items:center;justify-content:center}
.photo{position:absolute}

/* nav */
.nav{position:absolute;left:111px;top:18px;width:976px;height:84px;background:var(--white);display:flex;align-items:center;justify-content:space-between;padding:0 38px 0 32px}
.brand{display:flex;align-items:center;gap:10px;font-size:21px;font-weight:400;color:var(--ink);letter-spacing:.5px}
.brand .dot{width:14px;height:14px;border-radius:50%;background:var(--blue)}
.menu{display:flex;gap:30px;font-size:16px;font-weight:500;color:var(--ink)}

/* products */
.card{position:absolute;width:291px;height:366px;background:var(--white);border-radius:12px}
.card .thumb{position:absolute;left:60px;top:14px;width:171px;height:150px;border-radius:6px}
.card .divider{position:absolute;left:0;top:180px;width:291px;height:5px;background:var(--blue)}
.card .name{position:absolute;left:29px;top:213px;font-size:16px;color:var(--ink);text-transform:uppercase}
.card .desc{position:absolute;left:29px;top:253px;width:240px;font-size:14.5px;line-height:26px;color:var(--text)}
.card .base{position:absolute;left:0;bottom:-6px;width:291px;height:24px;border-bottom:5px solid var(--blue);border-left:5px solid var(--blue);border-right:5px solid var(--blue);border-radius:0 0 14px 14px}
.card .btn{left:36px;top:326px;width:250px;height:54px;font-size:15px}

/* form */
.field{position:absolute;left:663px;width:355px;border-bottom:1.5px solid #555;font-size:14px;color:#444;padding:0 0 8px 10px;text-transform:none}

/* footer */
.footer{background:var(--footer);color:var(--white)}
.contact-item{position:absolute;text-align:center;font-size:15px;line-height:28px;color:#e8e8e8}
.footer-menu{position:absolute;left:0;width:1200px;top:338px;display:flex;justify-content:center;gap:30px;font-size:16px;font-weight:500}
.socials{position:absolute;left:0;width:1200px;top:396px;display:flex;justify-content:center;gap:22px}
.socials span{width:14px;height:14px;border-radius:50%;background:var(--blue)}
</style>
</head>
<body>

<!-- HERO -->
<section class="section hero" style="top:0;height:690px">
  <div class="photo" role="img" aria-label="Laboratory glassware flasks and beakers in a bright blue lab" style="left:0;top:0;width:1200px;height:690px;background:linear-gradient(90deg,#eef6fc 0%,#e0effa 35%,#b8dcf3 55%,#8fc5ea 75%,#6fb3e3 100%)"></div>
  <div class="abs" style="left:0;top:0;width:640px;height:690px;background:linear-gradient(90deg,rgba(255,255,255,.75),rgba(255,255,255,0))"></div>
  <svg class="abs" style="left:0;top:540px" width="1200" height="150" viewBox="0 0 1200 150" preserveAspectRatio="none">
    <path d="M0 60 C200 140 520 90 760 55 C950 28 1100 40 1200 60 L1200 150 L0 150 Z" fill="#1a93d6"/>
    <path d="M0 85 C220 160 520 110 760 78 C950 52 1100 58 1200 72 L1200 150 L0 150 Z" fill="#ffffff"/>
  </svg>
  <nav class="nav">
    <div class="brand"><span class="dot"></span>NUVEXA LINK</div>
    <div class="menu"><span>HOME</span><span>ABOUT</span><span>OUR PRODUCT</span><span>WHAT WE DO</span><span>CONTACT</span></div>
  </nav>
  <div class="rule" style="left:111px;top:182px"></div>
  <h1 class="heading" style="left:111px;top:200px;font-size:57px;line-height:64px">WELCOME TO<br>NUVEXA LINK</h1>
  <p class="para" style="left:108px;top:350px;width:460px;font-size:16px;text-align:left">Lorem ipsum dolor sit amet, consectetur adipiscing elit, sed do eiusmod tempor incididunt ut labore et dolore magna aliqua.</p>
  <div class="btn" style="left:111px;top:464px;width:194px">Get Started
    <span class="circle"><svg width="28" height="14" viewBox="0 0 28 14"><path d="M1 7h24M19 1l6 6-6 6" stroke="#0f9ad8" stroke-width="2.6" fill="none" stroke-linecap="round" stroke-linejoin="round"/></svg></span></div>
</section>

<!-- ABOUT -->
<section class="section about" style="top:690px;height:582px">
  <div class="abs" style="left:0;top:66px;width:70px;height:422px;background:var(--blue)"></div>
  <div class="photo" role="img" aria-label="Gloved hand holding a test tube of yellow liquid over a rack of tubes" style="left:53px;top:66px;width:490px;height:422px;border-radius:14px;background:linear-gradient(135deg,#1e4f8e 0%,#5f93c9 40%,#d9e9f6 75%,#f3f8fc 100%)"></div>
  <div class="rule" style="left:601px;top:68px"></div>
  <h2 class="heading" style="left:601px;top:85px;font-size:38px">ABOUT US</h2>
  <p class="para" style="left:600px;top:148px;width:489px">Lorem ipsum dolor sit amet, consectetur adipiscing elit, sed do eiusmod tempor incididunt ut labore et dolore magna aliqua. Ut enim ad minim veniam, quis nostrud exercitation ullamco laboris nisi ut aliquip ex ea commodo consequat. Duis aute irure dolor in reprehenderit in voluptate velit esse cillum dolore eu fugiat nulla pariatur. Excepteur sint occaecat cupidatat non proident, sunt in culpa qui officia deserunt mollit anim</p>
  <div class="btn" style="left:596px;top:424px;width:194px">Read More
    <span class="circle"><svg width="28" height="14" viewBox="0 0 28 14"><path d="M1 7h24M19 1l6 6-6 6" stroke="#0f9ad8" stroke-width="2.6" fill="none" stroke-linecap="round" stroke-linejoin="round"/></svg></span></div>
</section>

<!-- PRODUCTS -->
<section class="section products" style="top:1272px;height:1350px;background:var(--grey-bg)">
  <div class="rule" style="left:465px;top:100px"></div>
  <h2 class="heading" style="left:0;width:1200px;text-align:center;top:116px;font-size:38px">OUR PRODUCTS</h2>
  <p class="para" style="left:160px;top:190px;width:880px;text-align:center;font-size:16.5px">Lorem ipsum dolor sit amet, consectetur adipiscing elit, sed do eiusmod tempor incididunt ut labore et dolore magna aliqua. Ut enim ad minim veniam, quis nostrud exercitation ullamco laboris nisi ut</p>

  <div class="card" style="left:122px;top:306px">
    <div class="thumb" role="img" aria-label="Magnetic system filter unit" style="background:linear-gradient(180deg,#ffffff,#d8d8d8 45%,#2b2b2b 60%,#f4f4f4)"></div>
    <div class="divider"></div><div class="name">Clearvane Cyclone</div>
    <div class="desc">Filter for powerful magnetic filtration of system debris</div><div class="base"></div>
    <div class="btn">Product Details<span class="circle"><svg width="28" height="14" viewBox="0 0 28 14"><path d="M1 7h24M19 1l6 6-6 6" stroke="#0f9ad8" stroke-width="2.6" fill="none" stroke-linecap="round" stroke-linejoin="round"/></svg></span></div>
  </div>
  <div class="card" style="left:454px;top:306px">
    <div class="thumb" role="img" aria-label="Red power flushing pump" style="background:linear-gradient(180deg,#ffffff,#e8533a 40%,#c7321f 80%,#f4f4f4)"></div>
    <div class="divider"></div><div class="name">PurgeFlow P90</div>
    <div class="desc">Effective, easy cleaning for dirty heating systems</div><div class="base"></div>
    <div class="btn">Product Details<span class="circle"><svg width="28" height="14" viewBox="0 0 28 14"><path d="M1 7h24M19 1l6 6-6 6" stroke="#0f9ad8" stroke-width="2.6" fill="none" stroke-linecap="round" stroke-linejoin="round"/></svg></span></div>
  </div>
  <div class="card" style="left:785px;top:306px">
    <div class="thumb" role="img" aria-label="Blue and green test kit case" style="background:linear-gradient(180deg,#ffffff,#2f7fc8 30%,#4fa34a 55%,#2f6db8 85%,#ffffff)"></div>
    <div class="divider"></div><div class="name">PurgeFlow Test Kit</div>
    <div class="desc">For identifying problem areas on old hydronic heating systems</div><div class="base"></div>
    <div class="btn">Product Details<span class="circle"><svg width="28" height="14" viewBox="0 0 28 14"><path d="M1 7h24M19 1l6 6-6 6" stroke="#0f9ad8" stroke-width="2.6" fill="none" stroke-linecap="round" stroke-linejoin="round"/></svg></span></div>
  </div>

  <div class="card" style="left:122px;top:735px">
    <div class="thumb" role="img" aria-label="Two white chemical containers with blue labels" style="background:linear-gradient(180deg,#ffffff,#eef3f8 35%,#9fbde0 60%,#ffffff)"></div>
    <div class="divider"></div><div class="name">Q200 Solar Cleaner</div>
    <div class="desc">Ready-to-use cleaner for solar thermal systems</div><div class="base"></div>
    <div class="btn">Product Details<span class="circle"><svg width="28" height="14" viewBox="0 0 28 14"><path d="M1 7h24M19 1l6 6-6 6" stroke="#0f9ad8" stroke-width="2.6" fill="none" stroke-linecap="round" stroke-linejoin="round"/></svg></span></div>
  </div>
  <div class="card" style="left:454px;top:735px">
    <div class="thumb" role="img" aria-label="Teal labelled cleaner bottle" style="background:linear-gradient(180deg,#ffffff,#5fd0cf 40%,#37b5b8 75%,#ffffff)"></div>
    <div class="divider"></div><div class="name">Wardenvale W400 Cleaner</div>
    <div class="desc">For older closed loop hydronic heating systems</div><div class="base"></div>
    <div class="btn">Product Details<span class="circle"><svg width="28" height="14" viewBox="0 0 28 14"><path d="M1 7h24M19 1l6 6-6 6" stroke="#0f9ad8" stroke-width="2.6" fill="none" stroke-linecap="round" stroke-linejoin="round"/></svg></span></div>
  </div>
  <div class="card" style="left:785px;top:735px">
    <div class="thumb" role="img" aria-label="Red labelled treatment bottle" style="background:linear-gradient(180deg,#ffffff,#e23a3a 40%,#c42424 75%,#ffffff)"></div>
    <div class="divider"></div><div class="name">W200 Noise Reducer</div>
    <div class="desc">A non-acid, leave-in treatment for boiler noise</div><div class="base"></div>
    <div class="btn">Product Details<span class="circle"><svg width="28" height="14" viewBox="0 0 28 14"><path d="M1 7h24M19 1l6 6-6 6" stroke="#0f9ad8" stroke-width="2.6" fill="none" stroke-linecap="round" stroke-linejoin="round"/></svg></span></div>
  </div>

  <div class="btn" style="left:484px;top:1159px;width:235px;height:52px;font-size:15px">View All Product
    <span class="circle" style="width:44px;height:44px"><svg width="28" height="14" viewBox="0 0 28 14"><path d="M1 7h24M19 1l6 6-6 6" stroke="#0f9ad8" stroke-width="2.6" fill="none" stroke-linecap="round" stroke-linejoin="round"/></svg></span></div>
</section>

<!-- WHAT WE DO -->
<section class="section what" style="top:2622px;height:658px;overflow:hidden">
  <div class="photo" role="img" aria-label="Soft blurred laboratory glassware background" style="left:0;top:0;width:1200px;height:658px;background:linear-gradient(90deg,#f4f8fb 0%,#eaf2f8 45%,#dde9f2 70%,#cfe0ec 100%)"></div>
  <svg class="abs" style="left:640px;top:0" width="560" height="658" viewBox="0 0 560 658">
    <path d="M280 0 L560 0 L560 658 L120 658 C40 600 10 520 40 420 C80 290 180 140 280 0 Z" fill="#2aa7df"/>
  </svg>
  <div class="photo" role="img" aria-label="Round flask of glowing blue liquid in a dark lab" style="left:662px;top:0;width:538px;height:658px;clip-path:path('M280 0 L538 0 L538 658 L110 658 C35 600 10 520 38 425 C78 295 175 150 290 0 Z');background:radial-gradient(circle at 62% 60%,#3fd2f2 0%,#1386b8 30%,#0b3d5e 65%,#071a2a 100%)"></div>
  <svg class="abs" style="left:920px;top:319" width="1" height="1"></svg>
  <div class="abs" style="left:920px;top:2890px"></div>
  <svg class="abs" style="left:918px;top:322px" width="80" height="80" viewBox="0 0 80 80">
    <circle cx="40" cy="40" r="38" fill="#ffffff"/><circle cx="40" cy="40" r="32" fill="#1596d4"/>
    <path d="M33 26 L55 40 L33 54 Z" fill="#ffffff"/>
  </svg>
  <div class="rule" style="left:111px;top:122px"></div>
  <h2 class="heading" style="left:111px;top:140px;font-size:38px">WHAT WE DO</h2>
  <p class="para" style="left:110px;top:202px;width:489px">Lorem ipsum dolor sit amet, consectetur adipiscing elit, sed do eiusmod tempor incididunt ut labore et dolore magna aliqua. Ut enim ad minim veniam, quis nostrud exercitation ullamco laboris nisi ut aliquip ex ea commodo consequat. Duis aute irure dolor in reprehenderit in voluptate velit esse cillum dolore eu fugiat nulla pariatur. Excepteur sint occaecat cupidatat non proident, sunt in culpa qui officia deserunt mollit anim</p>
  <div class="btn" style="left:107px;top:478px;width:194px">Read More
    <span class="circle"><svg width="28" height="14" viewBox="0 0 28 14"><path d="M1 7h24M19 1l6 6-6 6" stroke="#0f9ad8" stroke-width="2.6" fill="none" stroke-linecap="round" stroke-linejoin="round"/></svg></span></div>
</section>

<!-- CONTACT -->
<section class="section contact" style="top:3280px;height:770px">
  <div class="photo" role="img" aria-label="Scientist wearing safety goggles in a laboratory" style="left:0;top:0;width:640px;height:770px;background:linear-gradient(90deg,#c9b2a2 0%,#d8dfe6 35%,#e8f0f7 65%,rgba(255,255,255,0) 100%)"></div>
  <div class="rule" style="left:601px;top:102px"></div>
  <h2 class="heading" style="left:601px;top:120px;font-size:38px">GET IN TOUCH</h2>
  <p class="para" style="left:601px;top:182px;width:489px">Lorem ipsum dolor sit amet, consectetur adipiscing elit, sed do eiusmod tempor incididunt ut labore et dolore magna aliqua.</p>
  <div class="field" style="top:326px">NAME</div>
  <div class="field" style="top:395px">EMAIL</div>
  <div class="field" style="top:471px">PHONE NUMBER</div>
  <div class="field" style="top:543px">Message</div>
  <div class="btn" style="left:663px;top:615px;width:194px">Submit
    <span class="circle"><svg width="28" height="14" viewBox="0 0 28 14"><path d="M1 7h24M19 1l6 6-6 6" stroke="#0f9ad8" stroke-width="2.6" fill="none" stroke-linecap="round" stroke-linejoin="round"/></svg></span></div>
</section>

<!-- FOOTER -->
<footer class="section footer" style="top:4050px;height:502px">
  <svg class="abs" style="left:220px;top:40px" width="20" height="28" viewBox="0 0 20 28"><path d="M10 1a8 8 0 0 0-8 8c0 6 8 17 8 17s8-11 8-17a8 8 0 0 0-8-8z" fill="#1596d4"/><circle cx="10" cy="9" r="3" fill="#0b0c0e"/></svg>
  <div class="contact-item" style="left:110px;top:76px;text-align:left;font-size:14.5px">Lorem ipsum dolor sit amet,<br>consectetur adipiscing elit, sed</div>
  <svg class="abs" style="left:614px;top:44px" width="24" height="24" viewBox="0 0 24 24"><path d="M5 2h4l2 5-3 2a12 12 0 0 0 7 7l2-3 5 2v4a2 2 0 0 1-2 2A19 19 0 0 1 3 4a2 2 0 0 1 2-2z" fill="#1596d4"/></svg>
  <div class="contact-item" style="left:530px;top:86px;width:200px;font-size:14.5px">+1 888 8888 8888</div>
  <svg class="abs" style="left:990px;top:45px" width="28" height="22" viewBox="0 0 28 22"><rect x="2" y="2" width="24" height="18" rx="2" fill="none" stroke="#1596d4" stroke-width="2.4"/><path d="M3 4l11 9 11-9" fill="none" stroke="#1596d4" stroke-width="2.4"/></svg>
  <div class="contact-item" style="left:880px;top:82px;width:245px;font-size:16px">nuvexalink.example</div>
  <div class="abs" style="left:111px;top:148px;width:974px;height:1px;background:#5a5a5a"></div>
  <div class="brand abs" style="left:0;width:1200px;top:252px;justify-content:center;color:#ffffff"><span class="dot"></span>NUVEXA LINK</div>
  <div class="footer-menu"><span>HOME</span><span>ABOUT</span><span>OUR PRODUCT</span><span>WHAT WE DO</span><span>CONTACT</span></div>
  <div class="socials"><span></span><span></span><span></span><span></span><span></span></div>
  <div class="abs" style="left:111px;top:454px;width:974px;height:1px;background:#5a5a5a"></div>
  <div class="abs" style="left:113px;top:470px;font-size:14px">© 2023&nbsp;&nbsp; Nuvexa Link</div>
  <div class="abs" style="left:1055px;top:470px;font-size:14px">C64</div>
</footer>

</body>
</html>
```